50 Page Catalog Full Redesign New Look

We are looking for a redesign of our Catalog,

We are looking for a modern redesign of our Catalog, with our new logo most of the products will be the same with some new products as well.
Please use colors in the new logo attached
Attached is our current design please see this for what product will go in the catulog
Updates

Designs look the same

Target Market(s)

Automotive

Font styles to use
Other font styles liked:
• Our Font is outfit

Colors

Designer to choose colors to be used in the design.

```html
<!DOCTYPE html>
<html lang="en">
<head>
<meta charset="utf-8">
<title>Number Plate Frames – Catalogue Spread</title>
<link rel="stylesheet" href="https://fonts.googleapis.com/css2?family=Outfit:wght@300;400;500;600&display=swap">
<style>
  :root{
    --bg:#efefef;
    --page-left:#e3e3e4;
    --page-right:#fbfbfb;
    --navy:#176a9c;
    --sky:#4a95c4;
    --card-blue:#1b6ba0;
    --card-sky:#3d8dc2;
    --card-grey:#d6d6d8;
    --ink:#2b2b2b;
    --white:#ffffff;
    --photo-a:#f4f4f4;
    --photo-b:#cfcfd1;
  }
  *{box-sizing:border-box;margin:0;padding:0}
  html,body{width:1200px;height:800px;overflow:hidden;background:var(--bg);font-family:"Outfit",sans-serif;color:var(--ink)}
  .spread{position:absolute;left:52px;top:1px;width:1096px;height:798px;display:flex;box-shadow:0 10px 30px rgba(0,0,0,.12)}
  .page{position:relative;width:548px;height:798px;overflow:hidden}
  .page--left{background:var(--page-left)}
  .page--right{background:var(--page-right)}
  .section-tab{position:absolute;top:0;width:278px;height:38px;display:flex;align-items:center;color:var(--white);font-weight:600;font-size:18px}
  .page--left .section-tab{left:0;background:var(--navy);border-bottom-right-radius:20px;padding-left:32px}
  .page--right .section-tab{right:0;background:var(--sky);border-bottom-left-radius:20px;justify-content:flex-end;padding-right:34px}
  .product{position:absolute}
  .product__photo{position:absolute;left:0;right:0;background:linear-gradient(160deg,var(--photo-a),var(--photo-b));border-radius:4px}
  .product__badge{position:absolute;width:40px;height:40px;border-radius:50%;background:#9ea3ab;border:3px solid #dcdcdc;right:-6px;top:-4px}
  .product__head{position:absolute;left:0;right:0;height:35px;color:var(--white);padding:5px 8px;display:flex;justify-content:space-between;align-items:flex-end;font-weight:500}
  .page--left .product__head{background:var(--card-blue)}
  .page--right .product__head{background:var(--card-sky)}
  .product__name{font-size:10.5px;line-height:1.15}
  .product__sku{font-size:8.5px;white-space:nowrap}
  .product__body{position:absolute;left:0;right:0;background:var(--card-grey);padding:7px 8px;font-size:7.2px;line-height:1.25;font-weight:300}
  .product__body b{font-weight:600}
  .product__body p{margin-bottom:5px}
  .footer-tab{position:absolute;bottom:0;width:278px;height:38px;display:flex;align-items:center;color:var(--white);font-size:9px;font-weight:300}
  .page--left .footer-tab{left:0;background:var(--navy);border-top-right-radius:20px;padding-left:12px}
  .page--right .footer-tab{right:0;background:var(--sky);border-top-left-radius:20px;justify-content:flex-end;padding-right:12px}
  .folio{font-size:15px;font-weight:600}
  .page--left .folio{margin-right:30px}
  .page--right .folio{margin-left:34px}
  .follow{position:absolute;left:33px;bottom:20px;display:flex;align-items:center;gap:7px;font-size:8px;font-weight:600;color:var(--card-sky)}
  .follow span.net{font-weight:500;color:var(--navy)}
</style>
</head>
<body>
<div class="spread">
  <section class="page page--left">
    <div class="section-tab">Number Plate Frames</div>

    <article class="product" style="left:33px;top:53px;width:235px">
      <div class="product__photo" style="top:0;height:198px" role="img" aria-label="Photo of white and black printed standard number plate frames"></div>
      <div class="product__badge"></div>
      <div class="product__head" style="top:204px"><span class="product__name">Standard 6 Digit<br>Number Plate Frames</span><span class="product__sku">SKU: BP12585</span></div>
      <div class="product__body" style="top:239px;height:107px">
        <p><b>Size:</b> W 375mm x H 135mm</p>
        <p><b>Description:</b><br>These Licence Plate Surrounds are made in Australia from ABS plastic and are the most effective way to promote your Dealership or brand.</p>
        <p><b>Branding Options:</b><br>● Screen Print ● Raised</p>
      </div>
    </article>

    <article class="product" style="left:286px;top:53px;width:228px">
      <div class="product__photo" style="top:0;height:198px" role="img" aria-label="Photo of white and black printed large number plate frames"></div>
      <div class="product__badge"></div>
      <div class="product__head" style="top:204px"><span class="product__name">Large 6 Digit<br>Number Plate Frames</span><span class="product__sku">SKU: BP12586</span></div>
      <div class="product__body" style="top:239px;height:107px">
        <p><b>Size:</b> W 375mm x H 152mm</p>
        <p><b>Description:</b><br>These Licence Plate Surrounds are made in Australia from ABS plastic and are the most effective way to promote your Dealership or brand. Larger Frames have a larger area at the bottom to Print on to make your logo easier to read.</p>
        <p><b>Branding Options:</b><br>● Screen Print ● Raised</p>
      </div>
    </article>

    <article class="product" style="left:33px;top:405px;width:235px">
      <div class="product__photo" style="top:0;height:190px" role="img" aria-label="Photo of plain white and black number plate frames"></div>
      <div class="product__badge"></div>
      <div class="product__head" style="top:197px"><span class="product__name">Plain Fronts 6 Digit<br>Number Plate Frames</span><span class="product__sku">SKU: BP12587</span></div>
      <div class="product__body" style="top:233px;height:109px">
        <p><b>Size:</b> W 375mm x H 135mm</p>
        <p><b>Description:</b><br>These Licence Plate Surrounds are made in Australia from ABS plastic. These Frames are not printed and are used to enhance the front number plate.</p>
        <p><b>Branding Options:</b><br>● Screen Print</p>
      </div>
    </article>

    <article class="product" style="left:286px;top:405px;width:228px">
      <div class="product__photo" style="top:0;height:190px" role="img" aria-label="Photo of printed white and black premium number plate frames"></div>
      <div class="product__badge"></div>
      <div class="product__head" style="top:194px"><span class="product__name">NSW Premium<br>Number Plate Frames</span><span class="product__sku">SKU: BP12588</span></div>
      <div class="product__body" style="top:230px;height:107px">
        <p><b>Size:</b> W 375mm x H 118mm</p>
        <p><b>Description:</b><br>These Licence Plate Surrounds are made in Australia from ABS plastic and are the most effective way to promote your Dealership or brand.</p>
        <p><b>Branding Options:</b><br>● Screen Print ● Raised</p>
      </div>
    </article>

    <div class="footer-tab"><span class="folio">6</span>1800 412 275 | sales@kerrin.com.au</div>
  </section>

  <section class="page page--right">
    <div class="section-tab">Number Plate Frames</div>

    <article class="product" style="left:33px;top:53px;width:230px">
      <div class="product__photo" style="top:0;height:172px" role="img" aria-label="Photo of plain white and black premium number plate frames"></div>
      <div class="product__badge"></div>
      <div class="product__head" style="top:179px"><span class="product__name">Plain Fronts - NSW Premium<br>Number Plate Frames</span><span class="product__sku">SKU: BP12589</span></div>
      <div class="product__body" style="top:214px;height:106px">
        <p><b>Size:</b> W 375mm x H 90mm</p>
        <p><b>Description:</b><br>These Licence Plate Surrounds are made in Australia from ABS plastic. These Frames are not printed and are used to enhance the front number plate.</p>
        <p><b>Branding Options:</b><br>● Screen Print</p>
      </div>
    </article>

    <article class="product" style="left:281px;top:53px;width:235px">
      <div class="product__photo" style="top:0;height:172px" role="img" aria-label="Photo of a perspex number plate cover with black border and lines"></div>
      <div class="product__badge"></div>
      <div class="product__head" style="top:177px"><span class="product__name">Standard 6 Digit<br>Number Plate Covers</span><span class="product__sku">SKU: BP12592</span></div>
      <div class="product__body" style="top:212px;height:108px">
        <p><b>Size:</b> W 375mm x H 135mm</p>
        <p><b>Description:</b><br>Quality perspex licence plate covers with black border - with or without lines.</p>
        <p><b>Branding Options:</b><br>● Screen Print</p>
      </div>
    </article>

    <article class="product" style="left:33px;top:383px;width:230px">
      <div class="product__photo" style="top:0;height:116px" role="img" aria-label="Photo of a slimline perspex number plate cover"></div>
      <div class="product__badge"></div>
      <div class="product__head" style="top:123px"><span class="product__name">QLD Slimline<br>Number Plate Covers</span><span class="product__sku">SKU: BP12590</span></div>
      <div class="product__body" style="top:158px;height:107px">
        <p><b>Size:</b> W 375mm x H 100mm</p>
        <p><b>Description:</b><br>Quality perspex licence plate covers with black border - with or without lines.</p>
        <p><b>Branding Options:</b><br>● Screen Print</p>
      </div>
    </article>

    <article class="product" style="left:281px;top:383px;width:235px">
      <div class="product__photo" style="top:0;height:118px" role="img" aria-label="Photo of a wide euro perspex number plate cover"></div>
      <div class="product__badge"></div>
      <div class="product__head" style="top:125px"><span class="product__name">Euro<br>Number Plate Covers</span><span class="product__sku">SKU: BP12591</span></div>
      <div class="product__body" style="top:160px;height:107px">
        <p><b>Size:</b> W 520mm x H 115mm</p>
        <p><b>Description:</b><br>Quality perspex licence plate covers with black border - with or without lines.</p>
        <p><b>Branding Options:</b><br>● Screen Print</p>
      </div>
    </article>

    <div class="follow">FOLLOW US <span class="net">Friendlink</span><span class="net">Worknet</span></div>
    <div class="footer-tab">kerrinpromotional.com.au<span class="folio">7</span></div>
  </section>
</div>
</body>
</html>
```